K SPIRES Business Card Design

Need a business card design for K Spires, we're a tower company - our main scope of work is to upgrade cellular sites: swap antennas, install new coax, fiber, replace mounts, etc. Mostly tower work.

would like to see a sharp business card design with our logo either on background or with tower image on the background - something describing our field not only in words but in images.

Target Market(s)

USA

Industry/Entity Type

Business

Contact Information for Business Card

Tarnek Obliva
Operations Manager
K Spires LLC

cell 555-318-2094
tarnek@k-spires-example.com

4185 Wexbridge Commerce Pkwy, Suite D
Norcross, GA, 30571

Requirements
Must have
• some tower related design
Nice to have
• some tower or cellular antennas on the background, if possible to compliment our logo...

```html
<!DOCTYPE html>
<html lang="en">
<head>
<meta charset="utf-8">
<title>K Spires Business Card</title>
<link href="https://fonts.googleapis.com/css2?family=Aldrich&display=swap" rel="stylesheet">
<style>
  :root {
    --navy: #2e2585;
    --green: #2f8f2f;
    --ink: #333338;
    --paper: #ffffff;
    --paper-shade: #e9e9ec;
    --stage: #e2e2e8;
    --white: #ffffff;
  }
  * { box-sizing: border-box; margin: 0; padding: 0; }
  html, body {
    width: 1200px;
    height: 840px;
    overflow: hidden;
    background: var(--stage);
    font-family: "Aldrich", sans-serif;
  }
  .card {
    position: absolute;
    left: 75px;
    top: 120px;
    width: 1050px;
    height: 600px;
    background: linear-gradient(160deg, var(--paper-shade) 0%, var(--paper) 45%, var(--paper) 100%);
    overflow: hidden;
    box-shadow: 0 10px 30px rgba(40, 40, 70, 0.18);
  }
  .card-waves {
    position: absolute;
    inset: 0;
    width: 100%;
    height: 100%;
  }
  .brand {
    position: absolute;
    right: 210px;
    top: 55px;
    display: flex;
    align-items: center;
    gap: 16px;
  }
  .brand-mark {
    width: 24px;
    height: 24px;
    background: var(--green);
  }
  .brand-name {
    font-size: 80px;
    line-height: 1;
    color: var(--navy);
  }
  .holder {
    position: absolute;
    right: 210px;
    top: 170px;
    text-align: right;
  }
  .holder-name {
    font-size: 30px;
    letter-spacing: 1px;
    color: var(--ink);
  }
  .holder-title {
    font-size: 22px;
    color: var(--navy);
    margin-top: 4px;
  }
  .address {
    position: absolute;
    right: 40px;
    top: 395px;
    text-align: right;
    font-size: 21px;
    line-height: 1.45;
    color: var(--white);
    font-style: normal;
  }
  .contacts {
    position: absolute;
    left: 40px;
    top: 400px;
    list-style: none;
    color: var(--white);
    font-size: 21px;
  }
  .contacts li {
    display: flex;
    align-items: center;
    gap: 14px;
    height: 37px;
  }
  .contact-icon {
    width: 22px;
    height: 22px;
    flex: none;
  }
</style>
</head>
<body>
  <main class="card">
    <svg class="card-waves" viewBox="0 0 1050 600" aria-hidden="true">
      <path fill="var(--green)" d="M0,365 C150,310 320,278 470,276 C330,290 170,328 0,392 Z"/>
      <path fill="var(--navy)" d="M0,402 C170,335 330,302 470,295 C350,310 200,350 0,426 Z"/>
      <path fill="var(--navy)" d="M0,436 C170,340 380,300 560,308 C720,316 880,312 960,268 C1005,240 1035,205 1050,175 L1050,600 L0,600 Z"/>
      <path fill="var(--green)" d="M830,300 C930,282 1005,220 1050,130 L1050,160 C1005,245 930,292 830,300 Z"/>
      <path fill="var(--white)" d="M470,314 C600,292 720,310 820,310 C720,325 600,310 470,314 Z"/>
    </svg>

    <div class="brand">
      <span class="brand-mark"></span>
      <span class="brand-name">K Spires</span>
    </div>

    <div class="holder">
      <p class="holder-name">TARNEK OBLIVA</p>
      <p class="holder-title">Operations Manager</p>
    </div>

    <address class="address">4185 Wexbridge Commerce Pkwy, Suite D<br>Norcross, GA, 30571</address>

    <ul class="contacts">
      <li>
        <svg class="contact-icon" viewBox="0 0 24 24" aria-hidden="true"><path fill="var(--white)" d="M6.6 10.8a15 15 0 0 0 6.6 6.6l2.2-2.2a1 1 0 0 1 1-.25 11 11 0 0 0 3.6.6 1 1 0 0 1 1 1V20a1 1 0 0 1-1 1A17 17 0 0 1 3 4a1 1 0 0 1 1-1h3.5a1 1 0 0 1 1 1 11 11 0 0 0 .6 3.6 1 1 0 0 1-.25 1z"/></svg>
        <span>555 318 2094</span>
      </li>
      <li>
        <svg class="contact-icon" viewBox="0 0 24 24" aria-hidden="true"><rect x="6" y="2" width="12" height="20" rx="2" fill="none" stroke="var(--white)" stroke-width="2"/><circle cx="12" cy="18" r="1.3" fill="var(--white)"/></svg>
        <span>555 318 2094</span>
      </li>
      <li>
        <svg class="contact-icon" viewBox="0 0 24 24" aria-hidden="true"><rect x="7" y="2" width="10" height="7" fill="var(--white)"/><rect x="3" y="9" width="18" height="13" rx="1" fill="var(--white)"/><rect x="7" y="13" width="10" height="2" fill="var(--navy)"/><rect x="7" y="17" width="10" height="2" fill="var(--navy)"/></svg>
        <span>555 318 2094</span>
      </li>
      <li>
        <svg class="contact-icon" viewBox="0 0 24 24" aria-hidden="true"><rect x="2" y="5" width="20" height="14" fill="var(--white)"/><path d="M2 5 L12 13 L22 5" fill="none" stroke="var(--navy)" stroke-width="1.8"/></svg>
        <span>tarnek@k-spires-example.com</span>
      </li>
      <li>
        <svg class="contact-icon" viewBox="0 0 24 24" aria-hidden="true"><g fill="none" stroke="var(--white)" stroke-width="1.8"><circle cx="12" cy="12" r="9.5"/><ellipse cx="12" cy="12" rx="4.5" ry="9.5"/><path d="M2.5 12h19M4 7h16M4 17h16"/></g></svg>
        <span>www.k-spires-example.com</span>
      </li>
    </ul>
  </main>
</body>
</html>
```